International Clinical Software Company needs a new business card design

We are looking for a new business card design for our company that has recently expanded into the UK market, making us a multinational company.
After having rebranded our website and produced a new style guide, we are looking for a business card that is creative and attention grabbing, while being consistent with the style and colour scheme used on the new website, www.plumvora.example
We produce care management technology for the aged care market, but the main aspect we aim to communicate is the human element of our software, and the way it assists in providing better care for aged people, and stronger relationships between aged people and the staff that care for them.
Our current business card is a dark green with gold text, which makes the text quite difficult to read, not very aesthetically appealing and the colour scheme looks quite dated.
We would like something fresh and modern, that can still be colourful but doesn't use large blocks of dark colour, and uses the colours within our logo.
Something tying in with the leaves that are used in our logo could work quite nicely, along with the Autumn/Fall colours of soft greens, yellows and reds (also in our existing logo). However also happy to look at fresh, completely out of the box ideas we may not have yet considered.
Target Market(s)
The people that receive this business card work in the aged card or health industry and are either corporate/management level staff or clinical (Registered Nurses, care workers etc.)
Industry/Entity Type
Health Product
Contact Information for Business Card
Company Name - BrindlewayCare
Company locations: United Kingdom, Australia, New Zealand
Staff Details:
Staff name: Derek Mallow
Staff job title: Executive Chairman
Staff email: d.mallow@plumvora.example
Office phone number: 01742 918576
Font styles to use
Other font styles liked:
- Calibri
Requirements
Must have
- Must include the BrindlewayCare brand name in it's current font
- Must include logo (3 leaves in gold circle)
- Must include Business Card Details
Nice to have
- Elements of gold
- White space
- Something autumn themed but not too cliched
Should not have
- No blue - used by a major competitor and we would like to differentiate from them
- Large blocks of dark green colour (the green that appears in our leaves on the logo on our current business card is the background colour and it is far too dark)

```html
<!DOCTYPE html>
<html lang="en">
<head>
<meta charset="utf-8">
<title>BrindlewayCare – Business Card</title>
<link rel="stylesheet" href="https://fonts.googleapis.com/css2?family=Carlito:wght@400;700&display=swap">
<style>
  :root {
    --page-bg: #ece9e4;
    --card-white: #ffffff;
    --gold: #b39f74;
    --gold-light: #d7c9a6;
    --gold-dark: #9c875c;
    --crimson: #c4144b;
    --text-grey: #7c7a77;
    --brand-grey: #a8a29a;
    --leaf-yellow: #efe6a0;
    --leaf-green: #c9d38e;
    --leaf-red: #d9a3a8;
    --leaf-plum: #b69aa0;
  }
  * { margin: 0; padding: 0; box-sizing: border-box; }
  html, body {
    width: 1200px; height: 950px; overflow: hidden;
    background: var(--page-bg);
    font-family: "Carlito", "Calibri", sans-serif;
  }
  .card {
    position: absolute; left: 75px; top: 175px;
    width: 1050px; height: 600px;
    border-radius: 34px; overflow: hidden;
    background: var(--card-white);
    box-shadow: 0 14px 40px rgba(60, 50, 40, 0.18);
  }
  .gold-band {
    position: absolute; left: 0; top: 0; bottom: 0; width: 220px;
    background: linear-gradient(90deg, var(--gold-dark), var(--gold) 55%, var(--gold-light));
  }
  .leaf-artwork {
    position: absolute; right: 0; top: 0; width: 620px; height: 600px;
    background:
      radial-gradient(circle at 70% 40%, var(--leaf-plum) 0, transparent 38%),
      radial-gradient(circle at 45% 25%, var(--leaf-yellow) 0, transparent 45%),
      radial-gradient(circle at 85% 70%, var(--leaf-green) 0, transparent 40%),
      radial-gradient(circle at 40% 75%, var(--leaf-red) 0, transparent 40%);
    opacity: 0.75;
    -webkit-mask-image: linear-gradient(90deg, transparent, #000 35%);
            mask-image: linear-gradient(90deg, transparent, #000 35%);
  }
  .brand {
    position: absolute; left: 160px; top: 62px;
    display: flex; align-items: center; gap: 22px;
  }
  .brand-mark {
    width: 120px; height: 120px; border-radius: 50%;
    background: var(--card-white);
    border: 6px solid var(--gold-light);
  }
  .brand-name {
    font-size: 60px; font-weight: 400; color: var(--brand-grey);
    letter-spacing: 0.5px;
  }
  .details { position: absolute; left: 300px; top: 210px; }
  .person-name { font-size: 44px; font-weight: 700; color: var(--gold); line-height: 1.1; }
  .person-title { font-size: 32px; font-weight: 400; color: var(--crimson); margin-bottom: 18px; }
  .locations { font-size: 30px; color: var(--text-grey); line-height: 1.2; margin-bottom: 16px; }
  .contact-list { list-style: none; font-size: 30px; color: var(--text-grey); line-height: 1.35; }
  .contact-list li { display: flex; align-items: center; gap: 14px; }
  .contact-icon { width: 24px; height: 24px; fill: var(--text-grey); flex: none; }
</style>
</head>
<body>
  <section class="card" aria-label="BrindlewayCare business card">
    <div class="gold-band"></div>
    <div class="leaf-artwork" role="img" aria-label="Soft autumn leaves in faded yellow, green, red and plum"></div>

    <header class="brand">
      <span class="brand-mark"></span>
      <span class="brand-name">BrindlewayCare</span>
    </header>

    <div class="details">
      <p class="person-name">Derek Mallow</p>
      <p class="person-title">Executive Chairman</p>
      <p class="locations">United Kingdom<br>Australia • New Zealand</p>
      <ul class="contact-list">
        <li>
          <svg class="contact-icon" viewBox="0 0 24 24" aria-hidden="true"><path d="M6.6 10.8a15.1 15.1 0 0 0 6.6 6.6l2.2-2.2a1 1 0 0 1 1-.25 11.4 11.4 0 0 0 3.6.57 1 1 0 0 1 1 1V20a1 1 0 0 1-1 1A17 17 0 0 1 3 4a1 1 0 0 1 1-1h3.5a1 1 0 0 1 1 1c0 1.25.2 2.45.57 3.57a1 1 0 0 1-.25 1z"/></svg>
          01742 918576
        </li>
        <li>
          <svg class="contact-icon" viewBox="0 0 24 24" aria-hidden="true"><path d="M3 5h18v14H3z M3 5l9 7 9-7" fill="none" stroke="#7c7a77" stroke-width="2"/></svg>
          d.mallow@plumvora.example
        </li>
        <li>
          <svg class="contact-icon" viewBox="0 0 24 24" aria-hidden="true"><circle cx="12" cy="12" r="9" fill="none" stroke="#7c7a77" stroke-width="2"/><path d="M3 12h18M12 3c3 3 3 15 0 18M12 3c-3 3-3 15 0 18" fill="none" stroke="#7c7a77" stroke-width="1.6"/></svg>
          www.plumvora.example
        </li>
      </ul>
    </div>
  </section>
</body>
</html>
```